wood grain ultrasonic essential oil aroma diffuser

Design a package that is simple but luxurious for the diffuser with my logo. My business is called “Open Petal Path”. The logo incorporates “Thoughts become things” the concept is positive thinking. I don’t particularly want the product featured as I have like to develop a uniform look for packaging and website and there are 2 different diffusers,

Target Market(s)

People interested in yoga, meditation, metaphysical aspects

Industry/Entity Type

Health And Wellness

Colors

Designer to choose colors to be used in the design.

Requirements
Must have
• Luxurious feel to packaging and alignment with the website

```html
<!DOCTYPE html>
<html lang="en">
<head>
<meta charset="utf-8">
<title>Open Petal Path – Diffuser Packaging</title>
<link rel="stylesheet" href="https://fonts.googleapis.com/css2?family=Josefin+Sans:wght@300;400&display=swap">
<style>
  :root {
    --canvas: #ffffff;
    --pack-light: #f6f6f6;
    --pack-light-side: #ececec;
    --pack-dark: #1c1a1b;
    --pack-dark-side: #141213;
    --gold: #a8803a;
    --band-a: #5a2d82;
    --band-b: #2f4fa8;
    --band-c: #3aa65a;
    --band-d: #d8b328;
    --band-e: #e0482e;
    --band-f: #b3263a;
    --band-g: #3b3340;
  }
  * { box-sizing: border-box; margin: 0; padding: 0; }
  html, body { width: 1200px; height: 1000px; overflow: hidden; background: var(--canvas); }
  body { font-family: "Josefin Sans", sans-serif; position: relative; }

  .package { position: absolute; top: 320px; height: 510px; display: flex; }
  .package--light { left: 95px; }
  .package--dark { left: 648px; }

  .panel { position: relative; height: 100%; overflow: hidden; }
  .panel--front { width: 360px; }
  .panel--side { width: 115px; }
  .package--light .panel--front { background: var(--pack-light); }
  .package--light .panel--side { background: var(--pack-light-side); }
  .package--dark .panel--front { background: var(--pack-dark); }
  .package--dark .panel--side { background: var(--pack-dark-side); }

  .brand { position: absolute; top: 100px; left: 0; right: 0; text-align: center; }
  .brand-mark { width: 88px; height: 88px; margin: 0 auto; border-radius: 50%; background: var(--gold); }
  .brand-name {
    margin-top: 22px; color: var(--gold); font-weight: 400;
    font-size: 22px; letter-spacing: 1px; white-space: nowrap;
  }

  .product-title {
    position: absolute; top: 300px; left: 0; right: 0; text-align: center;
    color: var(--gold); font-weight: 300; font-size: 20px; line-height: 25px;
    letter-spacing: 1.4px; white-space: nowrap;
  }

  .side-art {
    position: absolute; top: 140px; left: 18px; width: 80px; height: 110px;
    border-radius: 40% 40% 20% 20%;
    background: linear-gradient(180deg, transparent, rgba(168,128,58,0.18));
  }
  .side-title {
    position: absolute; top: 278px; left: 0; right: 0; text-align: center;
    color: var(--gold); font-weight: 300; font-size: 11.5px; line-height: 16px;
    letter-spacing: 0; white-space: nowrap;
  }

  .color-band {
    position: absolute; left: 0; right: 0; bottom: 0;
    background: linear-gradient(100deg,
      var(--band-a) 0%, var(--band-b) 14%, var(--band-g) 24%, var(--band-c) 34%,
      var(--band-d) 46%, var(--band-g) 56%, var(--band-e) 68%, var(--band-f) 80%, var(--band-g) 100%);
  }
  .panel--front .color-band { height: 128px; }
  .panel--side .color-band { height: 150px; }
</style>
</head>
<body>
  <section class="package package--light" aria-label="White diffuser box">
    <div class="panel panel--front">
      <div class="brand">
        <div class="brand-mark"></div>
        <p class="brand-name">Open Petal Path</p>
      </div>
      <h1 class="product-title">ULTRASONIC<br>ESSENTIAL OIL<br>AROMA DIFFUSER</h1>
      <div class="color-band" role="img" aria-label="Flowing rainbow ribbon pattern"></div>
    </div>
    <div class="panel panel--side">
      <div class="side-art" role="img" aria-label="Gold line drawing of the aroma diffuser"></div>
      <p class="side-title">ULTRASONIC<br>ESSENTIAL OIL<br>AROMA DIFFUSER</p>
      <div class="color-band" role="img" aria-label="Flowing rainbow ribbon pattern"></div>
    </div>
  </section>

  <section class="package package--dark" aria-label="Black diffuser box">
    <div class="panel panel--front">
      <div class="brand">
        <div class="brand-mark"></div>
        <p class="brand-name">Open Petal Path</p>
      </div>
      <h2 class="product-title">ULTRASONIC<br>ESSENTIAL OIL<br>AROMA DIFFUSER</h2>
      <div class="color-band" role="img" aria-label="Flowing rainbow ribbon pattern"></div>
    </div>
    <div class="panel panel--side">
      <div class="side-art" role="img" aria-label="Gold line drawing of the aroma diffuser"></div>
      <p class="side-title">ULTRASONIC<br>ESSENTIAL OIL<br>AROMA DIFFUSER</p>
      <div class="color-band" role="img" aria-label="Flowing rainbow ribbon pattern"></div>
    </div>
  </section>
</body>
</html>
```